Calm and Clear Wellness Flyer (new business startup)

One page...clear enough to be read if faxed. This mental health clinic treats depression/anxiety in kids and adults. It also treats opiate and alcohol addiction. It's in downtown Elmira, NY and the owner of the clinic is from Elmira NY, where it's located. This clinic does not take health insurance, so it charges a low rate of $75 a visit once they pay the $125 starting fee.
Updates

Target Market(s)

doctors offices, new patients

Industry/Entity Type

Doctor

Requirements
Must have
• see microsoft word document. pdf is printed on the company letterhead.
Nice to have
• a simplified map would be nice. if you can include the building it would be a plus. The same two fonts were used in the business cards and letter head (kennedy small caps boo*) and Refrigerator Delux.

```html
<!DOCTYPE html>
<html lang="en">
<head>
<meta charset="utf-8">
<title>Calm and Clear Wellness Flyer</title>
<link href="https://fonts.googleapis.com/css2?family=Catamaran:wght@400;500;700;800&display=swap" rel="stylesheet">
<style>
  :root {
    --orange: #ee7440;
    --orange-deep: #ea5a20;
    --blue: #1a93cb;
    --blue-band: #1b97cf;
    --ink: #1f1f1f;
    --paper: #ffffff;
    --stage: #d4d4d4;
  }
  * { margin: 0; padding: 0; box-sizing: border-box; }
  html, body { width: 1200px; height: 1200px; overflow: hidden; }
  body {
    background: var(--stage);
    font-family: "Catamaran", sans-serif;
    color: var(--ink);
    position: relative;
  }
  .flyer {
    position: absolute; left: 217px; top: 40px;
    width: 766px; height: 1120px;
    background: var(--paper);
    overflow: hidden;
  }
  .flyer > * { position: absolute; }
  .brand { left: 33px; top: 36px; display: flex; align-items: center; gap: 14px; }
  .brand-mark { width: 52px; height: 52px; border-radius: 50%; background: var(--orange); }
  .brand-name { font-size: 28px; font-weight: 800; color: var(--orange-deep); letter-spacing: -0.3px; }
  .photo-team {
    left: 0; top: 119px; width: 373px; height: 459px;
    background: linear-gradient(135deg, #e9eef2 0%, #f6f8fa 45%, #d9dfe4 100%);
  }
  .provider-panel {
    left: 373px; top: 119px; width: 393px; height: 246px;
    background: var(--orange); color: #fff; padding: 26px 0 0 36px;
  }
  .provider-name { font-size: 50px; font-weight: 500; line-height: 58px; letter-spacing: 0.3px; }
  .provider-title { font-size: 21px; font-weight: 400; line-height: 35px; margin-top: 10px; }
  .photo-building {
    left: 373px; top: 365px; width: 393px; height: 277px;
    background: linear-gradient(180deg, #6d9fd8 0%, #a9c6e6 22%, #8a4a36 40%, #6f3a2b 70%, #9b9a98 85%, #c9c9c7 100%);
  }
  .label {
    background: var(--blue); color: #fff; font-weight: 700;
    padding: 0 14px 0 26px; height: 30px; line-height: 32px; font-size: 20px;
  }
  .label-hours { left: 0; top: 594px; width: 110px; }
  .hours { left: 27px; top: 630px; font-size: 24px; color: var(--orange-deep); }
  .fee { left: 27px; font-size: 18px; white-space: nowrap; display: flex; align-items: baseline; }
  .fee-name { font-size: 24px; font-weight: 800; color: var(--blue); margin-right: 6px; }
  .fee-leader { display: inline-block; border-bottom: 1.5px dashed var(--ink); height: 1px; align-self: center; margin-top: 6px; }
  .fee-price { position: absolute; font-size: 40px; font-weight: 800; color: var(--orange-deep); }
  .fee-eval { top: 668px; }
  .fee-visit { top: 708px; }
  .ages { left: 27px; top: 752px; font-size: 31px; color: var(--blue); }
  .ages strong { color: var(--orange-deep); font-weight: 800; }
  .map {
    left: 487px; top: 778px; width: 242px; height: 180px;
    background: linear-gradient(160deg, #f1f2f2 0%, #e7e9ea 55%, #bcd9f2 70%, #eef0f0 85%);
  }
  .label-conditions { left: 0; top: 807px; width: 243px; }
  .conditions {
    left: 27px; top: 846px; list-style: none;
    display: grid; grid-template-columns: 317px auto; row-gap: 6px;
    font-size: 21px; line-height: 25px;
  }
  .conditions li { display: flex; align-items: center; gap: 12px; }
  .tick { width: 14px; height: 14px; flex: none; }
  .motto { left: 27px; top: 970px; font-size: 16px; color: var(--blue); }
  .footnote { left: 27px; top: 996px; width: 720px; font-size: 11.8px; line-height: 16px; }
  .footer {
    left: 0; top: 1040px; width: 766px; height: 80px;
    background: var(--blue-band); color: #fff;
    display: flex; align-items: center;
  }
  .contact { display: flex; align-items: center; gap: 14px; }
  .contact-phone { padding-left: 46px; width: 318px; font-size: 31px; letter-spacing: 1px; border-right: 1.5px solid #fff; height: 46px; }
  .contact-web { padding-left: 26px; width: 277px; font-size: 18px; border-right: 1.5px solid #fff; height: 46px; }
  .contact-web b { font-weight: 700; }
  .social { padding-left: 32px; font-size: 19px; font-weight: 500; }
  .social-icons { display: flex; gap: 14px; margin-top: 2px; padding-left: 1px; }
  .social-icons span { width: 20px; height: 20px; border-radius: 50%; background: #fff; display: block; }
</style>
</head>
<body>
<main class="flyer">
  <header class="brand">
    <span class="brand-mark"></span>
    <span class="brand-name">CALM &amp; CLEAR WELLNESS</span>
  </header>

  <div class="photo-team" role="img" aria-label="Photo of two clinicians in white coats"></div>

  <section class="provider-panel">
    <h1 class="provider-name">DANIEL<br>REYES, RPA, PLLC</h1>
    <p class="provider-title">Psychiatric Physician Assistant<br>(PA-C, PSY-CQA)</p>
  </section>

  <div class="photo-building" role="img" aria-label="Photo of the brick clinic building on a downtown corner"></div>

  <div class="label label-hours">Hours:</div>
  <p class="hours">Monday and Saturdays 9-4pm</p>

  <p class="fee fee-eval"><span class="fee-name">Psychiatric Evaluation</span>(45min)<span class="fee-leader" style="width:205px"></span></p>
  <span class="fee-price" style="left:584px;top:654px">$125*</span>
  <p class="fee fee-visit"><span class="fee-name">Psychiatric Office Visit</span>(15min)<span class="fee-leader" style="width:207px"></span></p>
  <span class="fee-price" style="left:586px;top:694px">$75*</span>

  <p class="ages"><strong>Ages:</strong> 6 years old and up</p>

  <div class="map" role="img" aria-label="Street map showing the clinic location downtown by the river"></div>

  <div class="label label-conditions">Conditions Treated:</div>
  <ul class="conditions">
    <li><svg class="tick" viewBox="0 0 14 14"><circle cx="7" cy="7" r="7" fill="#ea5a20"/><path d="M3.8 7.2l2.2 2.2 4.2-4.4" stroke="#fff" stroke-width="1.8" fill="none"/></svg>Depression</li>
    <li><svg class="tick" viewBox="0 0 14 14"><circle cx="7" cy="7" r="7" fill="#ea5a20"/><path d="M3.8 7.2l2.2 2.2 4.2-4.4" stroke="#fff" stroke-width="1.8" fill="none"/></svg>PTSD</li>
    <li><svg class="tick" viewBox="0 0 14 14"><circle cx="7" cy="7" r="7" fill="#ea5a20"/><path d="M3.8 7.2l2.2 2.2 4.2-4.4" stroke="#fff" stroke-width="1.8" fill="none"/></svg>Anxiety</li>
    <li><svg class="tick" viewBox="0 0 14 14"><circle cx="7" cy="7" r="7" fill="#ea5a20"/><path d="M3.8 7.2l2.2 2.2 4.2-4.4" stroke="#fff" stroke-width="1.8" fill="none"/></svg>Bipolar</li>
    <li><svg class="tick" viewBox="0 0 14 14"><circle cx="7" cy="7" r="7" fill="#ea5a20"/><path d="M3.8 7.2l2.2 2.2 4.2-4.4" stroke="#fff" stroke-width="1.8" fill="none"/></svg>Childhood Mood Disorders</li>
    <li><svg class="tick" viewBox="0 0 14 14"><circle cx="7" cy="7" r="7" fill="#ea5a20"/><path d="M3.8 7.2l2.2 2.2 4.2-4.4" stroke="#fff" stroke-width="1.8" fill="none"/></svg>ADHD</li>
    <li><svg class="tick" viewBox="0 0 14 14"><circle cx="7" cy="7" r="7" fill="#ea5a20"/><path d="M3.8 7.2l2.2 2.2 4.2-4.4" stroke="#fff" stroke-width="1.8" fill="none"/></svg>&nbsp;Addiction</li>
    <li><svg class="tick" viewBox="0 0 14 14"><circle cx="7" cy="7" r="7" fill="#ea5a20"/><path d="M3.8 7.2l2.2 2.2 4.2-4.4" stroke="#fff" stroke-width="1.8" fill="none"/></svg>Disorders</li>
  </ul>

  <p class="motto">“We work for you, not the insurance companies”</p>
  <p class="footnote">*Although we do not partner with any Health Insurance Companies at this time, a bill will be provided to you at the time of service for you to submit to your insurance company.</p>

  <footer class="footer">
    <div class="contact contact-phone">
      <svg width="30" height="30" viewBox="0 0 30 30"><circle cx="15" cy="15" r="13.5" fill="none" stroke="#fff" stroke-width="2"/><path d="M10 8.5c1-.8 2-.6 2.6.4l1.2 2c.5.8.3 1.6-.4 2.1l-.9.6c.7 1.8 2 3.2 3.8 4l.7-.9c.5-.7 1.4-.9 2.1-.4l2 1.2c1 .6 1.1 1.7.3 2.6-1.5 1.6-3.6 1.7-6 .3-3-1.8-5.3-4.8-6.1-7.6-.5-1.8-.2-3.3.7-4.3z" fill="#fff"/></svg>
      <span>607 555 0148</span>
    </div>
    <div class="contact contact-web">
      <svg width="22" height="22" viewBox="0 0 22 22" fill="none" stroke="#fff" stroke-width="1.4"><circle cx="11" cy="11" r="9.5"/><ellipse cx="11" cy="11" rx="4.2" ry="9.5"/><path d="M1.5 11h19M3 6h16M3 16h16"/></svg>
      <span>www.<b>calm-clear</b>.com</span>
    </div>
    <div class="social">
      <p>Follow Us:</p>
      <div class="social-icons"><span></span><span></span><span></span></div>
    </div>
  </footer>
</main>
</body>
</html>
```